Stylish Business Cards Wanted

- DOUBLE SIDED Design Required -

High end, edgy cards for a corporate and personal stylist. Must include logo,
Name: Belinda Harwick
Title: Director and Stylist
telephone : +61 8 7142 5809
email: belinda@theloombriefing.example
website: theloombriefing.example
Tag: Corporate Workwear & Uniform Specialist | Personal Stylist
Would like nice icons for telephone, email, website

Target Market(s)

Businesses wanting stylish uniforms, people wanting stylish wardrobes

Industry/Entity Type

Corporate Workwear Stylist

Contact Information for Business Card

I would like black, white and gold foiling incorporated in the design - possibly a touch of the other colours on my branding guide attached Name: Belinda Harwick Title: Director and Stylist telephone : +61 8 7142 5809 email: belinda@theloombriefing.example website: theloombriefing.example Tag: Corporate Workwear & Uniform Specialist | Personal Stylist Would like nice icons for telephone, email, website

Font styles to use
Other font styles liked:
• Raleway

Colors

Designer to choose colors to be used in the design.

Requirements
Must have
• Gold foil accents

```html
<!DOCTYPE html>
<html lang="en">
<head>
<meta charset="UTF-8">
<title>The Loom Briefing — Business Cards</title>
<link href="https://fonts.googleapis.com/css2?family=Raleway:wght@600;700&family=Roboto:wght@400;500&family=Satisfy&display=swap" rel="stylesheet">
<style>
  :root {
    --backdrop: #2b2b2d;
    --card: #ffffff;
    --card-front: #f7f6f4;
    --gold: #d9a928;
    --navy: #1d2340;
    --ink: #22253a;
    --rose: #e07fa6;
  }
  * { box-sizing: border-box; margin: 0; padding: 0; }
  html, body {
    width: 799px; height: 1200px; overflow: hidden;
    background: var(--backdrop);
  }
  .sheet { position: relative; width: 799px; height: 1200px; }
  .card {
    position: absolute; left: 80px; width: 640px; height: 366px;
    border-radius: 24px; background: var(--card);
  }
  .card--front { top: 110px; background: var(--card-front); }
  .card--back { top: 724px; }

  .front-brand {
    position: absolute; inset: 0;
    display: flex; align-items: center; justify-content: center;
    font-family: "Raleway", sans-serif; font-weight: 700;
    font-size: 50px; letter-spacing: 1px; color: var(--gold);
  }

  .back-brand {
    position: absolute; left: 36px; top: 108px; width: 240px;
    font-family: "Raleway", sans-serif; font-weight: 700;
    font-size: 28px; line-height: 1.15; color: var(--navy);
  }
  .divider {
    position: absolute; left: 300px; top: 64px; width: 1.5px; height: 170px;
    background: var(--rose);
  }
  .contact { position: absolute; left: 326px; top: 62px; }
  .contact__name {
    font-family: "Satisfy", cursive; font-size: 31px; color: var(--gold); line-height: 1.1;
  }
  .contact__title {
    font-family: "Roboto", sans-serif; font-weight: 500; font-size: 15px;
    color: var(--ink); margin: 2px 0 14px;
  }
  .contact__list { list-style: none; }
  .contact__item {
    display: flex; align-items: center; gap: 12px;
    font-family: "Roboto", sans-serif; font-size: 16px; color: var(--ink);
    margin-bottom: 7px;
  }
  .contact__icon { width: 15px; height: 15px; flex: none; }
  .tagline {
    position: absolute; left: 36px; bottom: 40px;
    font-family: "Satisfy", cursive; font-size: 19px; color: var(--navy);
    display: flex; align-items: center; gap: 12px;
  }
  .tagline__bar { width: 2px; height: 20px; background: var(--gold); }
</style>
</head>
<body>
<main class="sheet">
  <section class="card card--front">
    <div class="front-brand">The Loom Briefing</div>
  </section>

  <section class="card card--back">
    <div class="back-brand">The Loom Briefing</div>
    <div class="divider"></div>
    <div class="contact">
      <p class="contact__name">Belinda Harwick</p>
      <p class="contact__title">Director and Stylist</p>
      <ul class="contact__list">
        <li class="contact__item">
          <svg class="contact__icon" viewBox="0 0 16 16" fill="none" stroke="#d9a928" stroke-width="1.4">
            <circle cx="8" cy="8" r="7"/>
            <path d="M5.6 4.6l1.2 1.6-.7 1c.5 1 1.2 1.7 2.2 2.2l1-.7 1.6 1.2-.8 1.2c-2.5-.3-5-2.8-5.3-5.3z" fill="#d9a928" stroke="none"/>
          </svg>
          +61 8 7142 5809
        </li>
        <li class="contact__item">
          <svg class="contact__icon" viewBox="0 0 16 16" fill="none" stroke="#d9a928" stroke-width="1.4">
            <rect x="1.5" y="3.5" width="13" height="9" rx="1"/>
            <path d="M1.8 4l6.2 5 6.2-5"/>
          </svg>
          belinda@theloombriefing.example
        </li>
        <li class="contact__item">
          <svg class="contact__icon" viewBox="0 0 16 16" fill="none" stroke="#d9a928" stroke-width="1.3">
            <circle cx="8" cy="8" r="6.6"/>
            <ellipse cx="8" cy="8" rx="2.8" ry="6.6"/>
            <path d="M1.4 8h13.2M2.4 4.8h11.2M2.4 11.2h11.2"/>
          </svg>
          www.theloombriefing.example
        </li>
      </ul>
    </div>
    <p class="tagline">
      <span>Corporate Workwear &amp; Uniform Specialist</span>
      <span class="tagline__bar"></span>
      <span>Personal Stylist</span>
    </p>
  </section>
</main>
</body>
</html>
```